Professional, Attractive, Simple Website Needed!!

We completed the design for our logo.

We need a website built out around this.

Here are a couple samples of how we want ours formatted.

http://brimvoltco.com

http://www.ravelbeam.com/lp/free-quote?LeadSource=Search%20Engine&ProgramName=searchads&experience=qual&language=en&type=brd&gclid=Xk7PLmqwTRZBNVuEYcaHdFgWsLoPeRtQnMxVbCzJaKiOuYtReWqAsDfGhJkLzXcVbNmQwErTyUiOpAsDfGhJkLzX_wcB

http://quorel.co
Updates

Project Deadline Extended
Reason: Extending this deadline due to our delay in providing designers with content for each page. This is coming in next 24 hours.

Project Deadline Extended
Reason: Due to scheduling conflicts and extended travel delays related to Puerto Rico, the deadline has been extended. Your patience is greatly appreciated.

Project Deadline Extended
Reason: Travel and scheduling conflicts have made it impossible to give this project the thorough review it deserves, therefore I am extending the deadline. Thank you for your patience!

Target Market(s)

Home Owners who earn 60k + household annually

Industry/Entity Type

It Professional

Coding

Coded - Design and coding required

Number of Pages Required

5+ page

Font styles to use
Serif

Colors
34a7d8
9bcb3c

Requirements
Must have
• Simple
• Lead form Entry (Ability for visitor to enter Name, number and address for a quote)
• Sleek Design
• Professional
• Testimonials
• Use color Scheme of Design Logo Attached
Nice to have
• Video when site starts
• Like this
• https://www.vidplexa.com/watch?v=Qm8rTbLw3Np&feature=vidplexa.be
Should not have
• Should not include Commercial solar
• Should not include wind power

```html
<!DOCTYPE html>
<html lang="en">
<head>
<meta charset="utf-8">
<title>Helioma Energy — Solar Savings</title>
<link rel="stylesheet" href="https://fonts.googleapis.com/css2?family=Lato:wght@400;700;900&family=Open+Sans:wght@400;600;700&display=swap">
<style>
:root{
  --blue:#34a7d8;
  --green:#9bcb3c;
  --green-dark:#7fb02a;
  --ink:#3a3a3a;
  --muted:#6d6d6d;
  --dark:#1f2326;
  --dark-2:#2a2f33;
  --white:#ffffff;
}
*{box-sizing:border-box;margin:0;padding:0}
html,body{width:1200px;height:3782px;overflow:hidden}
body{position:relative;font-family:"Open Sans",Arial,sans-serif;color:var(--ink);background:var(--white)}
a{text-decoration:none}
.abs{position:absolute}
h1,h2,h3,h4{font-family:"Lato",Arial,sans-serif}

/* hero */
.hero{left:0;top:0;width:1200px;height:760px;overflow:hidden}
.hero-photo{position:absolute;inset:0;background:linear-gradient(180deg,#c8b9a4 0%,#e9c79a 30%,#d7b287 45%,#5d7a8a 55%,#4f6e3e 75%,#3f6a26 100%)}
.hero-shapes{position:absolute;left:0;top:0}
.brand{position:absolute;left:70px;top:40px;display:flex;align-items:center;gap:10px}
.brand-dot{width:26px;height:26px;border-radius:50%;background:var(--blue)}
.brand-name{font-family:"Lato",sans-serif;font-weight:900;font-size:22px;color:var(--blue);letter-spacing:.5px}
.nav{position:absolute;right:80px;top:34px;display:flex;gap:22px}
.nav a{color:var(--white);font-family:"Lato",sans-serif;font-weight:700;font-size:15px}
.hero-title{position:absolute;left:0;width:1200px;top:200px;text-align:center;color:var(--white);font-weight:900;font-size:46px;line-height:56px;letter-spacing:1px;text-shadow:0 2px 6px rgba(0,0,0,.25)}
.hero-btns{position:absolute;left:0;width:1200px;top:408px;display:flex;justify-content:center;gap:8px}
.btn{display:inline-block;padding:0 40px;height:54px;line-height:54px;color:var(--white);font-family:"Lato",sans-serif;font-size:20px;text-transform:uppercase}
.btn-green{background:var(--green)}
.btn-blue{background:var(--blue)}
.hero-sq1{left:860px;top:548px;width:80px;height:60px;background:var(--green)}
.hero-sq2{left:893px;top:510px;width:82px;height:66px;background:var(--blue)}

/* why intro */
.section-title{font-weight:700;color:var(--blue);font-size:36px}
.why-title{left:80px;top:798px}
.why-text{left:80px;top:866px;width:520px;font-size:13.5px;line-height:22px;color:var(--muted)}
.why-btn{left:78px;top:1010px;height:56px;line-height:56px;padding:0 28px;font-size:19px;background:var(--green);color:var(--white);font-family:"Lato",sans-serif;text-transform:uppercase;display:flex;align-items:center;gap:12px}
.video{left:622px;top:806px;width:500px;height:262px;background:linear-gradient(135deg,#8fa3b3,#5b6f7e 55%,#2f3b44);overflow:hidden}
.video-bar{position:absolute;left:8px;right:8px;bottom:8px;height:32px;background:rgba(0,0,0,.75);display:flex;align-items:center;gap:10px;padding:0 10px;color:var(--white);font-size:13px;font-weight:700}
.video-track{flex:1;height:8px;border:1px solid #ccc}
.video-side{position:absolute;right:8px;top:10px;display:flex;flex-direction:column;gap:6px}
.video-side span{width:28px;height:28px;background:rgba(0,0,0,.75);display:block;border-radius:2px}

/* process */
.process{left:0;top:1127px;width:1200px;height:625px;background:radial-gradient(ellipse at 55% 60%,#3a4a3f 0%,#252b2e 45%,var(--dark) 100%)}
.process-title{position:absolute;top:58px;width:1200px;text-align:center;color:var(--blue);font-size:36px;font-weight:700}
.process-text{position:absolute;top:118px;left:250px;width:700px;text-align:center;color:#d9d9d9;font-size:13.5px;line-height:24px}
.step-label{position:absolute;color:var(--white);font-family:"Lato",sans-serif;font-size:23px;text-align:center;width:240px}

/* testimonial */
.quote-badge{left:554px;top:1706px;width:92px;height:92px}
.testi-title{left:0;top:1812px;width:1200px;text-align:center}
.avatar{left:530px;top:1890px;width:140px;height:140px;border-radius:50%;border:5px solid #e6e6e6;background:linear-gradient(160deg,#e9e9e9,#c9b8a7)}
.testi-text{left:200px;top:2070px;width:800px;text-align:center;font-size:13.5px;line-height:24px;color:var(--muted)}
.testi-name{left:0;top:2170px;width:1200px;text-align:center;font-weight:700;font-size:16px;color:#555}

/* benefits + form */
.split{left:0;top:2230px;width:1200px;height:468px;background:linear-gradient(100deg,var(--green) 0%,#8cc14a 35%,#5fb3a0 60%,var(--blue) 100%)}
.split-title{position:absolute;color:var(--white);font-size:36px;font-weight:700;top:42px}
.divider{position:absolute;left:598px;top:42px;height:380px;border-left:2px dashed rgba(255,255,255,.8)}
.benefit{position:absolute;left:78px;display:flex;gap:22px;width:520px}
.benefit-icon{width:70px;height:70px;border-radius:50%;background:var(--blue);flex:none;display:flex;align-items:center;justify-content:center;box-shadow:0 0 0 4px rgba(255,255,255,.25)}
.benefit h4{color:var(--white);font-size:20px;font-weight:700;margin-bottom:2px}
.benefit p{color:var(--white);font-size:13.5px;line-height:22px}
.benefit b{font-weight:700;text-transform:uppercase}
.field{position:absolute;left:643px;width:436px;height:42px;border:1.5px solid rgba(255,255,255,.85);color:var(--white);font-size:13.5px;padding:10px 10px}
.submit{position:absolute;left:864px;top:2553px;width:214px;height:42px;line-height:42px;text-align:center;background:var(--green);color:var(--white);font-family:"Lato",sans-serif;font-size:20px}

/* blog */
.blog-title{left:0;top:2754px;width:1200px;text-align:center}
.card{position:absolute;top:2894px;width:335px}
.card-img{height:190px}
.card-avatar{position:absolute;left:5px;top:-48px;width:96px;height:96px;border-radius:50%;border:5px solid var(--white);box-shadow:0 0 0 1px #ddd;background:linear-gradient(160deg,#eeeeee,#c7b29c)}
.card-meta{display:flex;gap:14px;margin-top:14px;align-items:flex-start}
.card-date{background:var(--blue);color:var(--white);font-size:13.5px;padding:12px 14px;white-space:nowrap}
.card-head{color:var(--blue);font-family:"Lato",sans-serif;font-weight:700;font-size:19px;line-height:22px;width:150px}
.card-text{margin-top:12px;font-size:13.5px;line-height:23px;color:var(--muted)}
.card-text b{color:var(--green-dark);text-decoration:underline;font-weight:700}

/* footer */
.footer{left:0;top:3280px;width:1200px;height:440px}
.foot-col{position:absolute;color:#e6e6e6;font-size:13.5px;line-height:24px}
.foot-col h4{color:var(--green);font-size:19px;font-weight:700;margin-bottom:14px}
.foot-brand{display:flex;align-items:center;gap:10px;margin-bottom:28px}
.foot-brand .brand-dot{width:30px;height:30px}
.foot-brand .brand-name{font-size:24px;color:var(--blue)}
.foot-row{display:flex;align-items:flex-start;gap:14px;margin-bottom:10px}
.foot-row svg{flex:none;margin-top:3px}
.social{display:flex;align-items:center;gap:14px;margin-bottom:13px}
.social i{width:30px;height:30px;border-radius:50%;background:var(--white);display:block}
.social i.first{background:var(--green)}
.bottom-bar{left:0;top:3718px;width:1200px;height:64px;background:var(--green);color:var(--white);text-align:center;line-height:64px;font-size:14px}
.bottom-bar b{font-weight:700}
</style>
</head>
<body>

<header class="abs hero">
  <div class="hero-photo" role="img" aria-label="Solar panel field on green grass under a warm sunset sky"></div>
  <svg class="hero-shapes" width="1200" height="760" viewBox="0 0 1200 760">
    <polygon points="0,0 520,0 0,300" fill="#9bcb3c"/>
    <polygon points="0,0 420,0 0,200" fill="#ffffff" opacity=".9"/>
    <polygon points="430,0 1200,0 1200,70 460,80" fill="#34a7d8"/>
    <path d="M0,640 C230,780 470,680 720,700 C930,716 1060,740 1200,690 L1200,760 L0,760 Z" fill="#34a7d8"/>
    <path d="M0,660 C240,790 480,700 720,716 C940,730 1070,750 1200,712 L1200,760 L0,760 Z" fill="#9bcb3c"/>
    <path d="M0,690 C250,800 490,725 720,735 C950,745 1080,765 1200,740 L1200,760 L0,760 Z" fill="#ffffff"/>
  </svg>
  <div class="brand"><span class="brand-dot"></span><span class="brand-name">HELIOMA ENERGY</span></div>
  <nav class="nav">
    <a href="#">Home</a><a href="#">Why Helioma Energy</a><a href="#">How it Works</a><a href="#">Testimonial</a><a href="#">Blog</a><a href="#">Contact</a>
  </nav>
  <h1 class="hero-title">SOLAR SAVINGS<br>WITH<br>HELIOMA ENERGY</h1>
  <div class="hero-btns"><a class="btn btn-green" href="#">Learn More</a><a class="btn btn-blue" href="#">Contact Us</a></div>
  <div class="abs hero-sq1"></div>
  <div class="abs hero-sq2"></div>
</header>

<section>
  <h2 class="abs section-title why-title">Why Helioma Energy</h2>
  <p class="abs why-text">Lorem Ipsum is simply dummy text of the printing and typesetting industry. Lorem Ipsum has been the industry's standard dummy text ever since the 1500s, when an unknown printer took a galley of type and scrambled it to make a type specimen book. It has survived not only five centuries.</p>
  <a class="abs why-btn" href="#">
    <svg width="22" height="18" viewBox="0 0 22 18"><rect x="1" y="4" width="20" height="13" rx="2" fill="#fff"/><rect x="7" y="1" width="8" height="4" fill="#fff"/><circle cx="11" cy="10.5" r="4" fill="#9bcb3c"/></svg>
    Check Out Our Work
  </a>
  <div class="abs video" role="img" aria-label="Video still of the team standing on a rooftop beside solar panels">
    <div class="video-side"><span></span><span></span><span></span></div>
    <div class="video-bar">
      <svg width="14" height="16" viewBox="0 0 14 16"><polygon points="0,0 14,8 0,16" fill="#fff"/></svg>
      <div class="video-track"></div><span>HD</span><span>playr</span>
    </div>
  </div>
</section>

<section class="abs process">
  <h2 class="process-title">Why Helioma Energy</h2>
  <p class="process-text">Lorem Ipsum is simply dummy text of the printing and typesetting industry. Lorem Ipsum has been the industry's standard dummy text ever since the 1500s</p>
  <svg class="abs" style="left:0;top:0" width="1200" height="625" viewBox="0 0 1200 625">
    <path d="M0,360 C120,300 300,330 504,285 C640,255 700,360 800,345 C900,330 950,270 1200,320" fill="none" stroke="#9bcb3c" stroke-width="1.5" stroke-dasharray="6 6"/>
    <g>
      <circle cx="202" cy="348" r="106" fill="none" stroke="#9bcb3c" stroke-dasharray="4 5"/>
      <circle cx="202" cy="348" r="92" fill="#34a7d8"/>
      <circle cx="202" cy="348" r="74" fill="#ffffff"/>
      <circle cx="202" cy="340" r="22" fill="#9bcb3c"/>
      <path d="M172,342 a30,30 0 0 1 60,0" fill="none" stroke="#9bcb3c" stroke-width="6"/>
      <rect x="166" y="338" width="12" height="20" rx="4" fill="#9bcb3c"/><rect x="226" y="338" width="12" height="20" rx="4" fill="#9bcb3c"/>
      <path d="M172,392 a30,24 0 0 1 60,0 Z" fill="#9bcb3c"/>
      <circle cx="334" cy="390" r="20" fill="#9bcb3c" stroke="#fff" stroke-width="3"/>
      <text x="334" y="397" text-anchor="middle" fill="#fff" font-family="Lato,sans-serif" font-size="18" font-weight="700">1</text>
    </g>
    <g>
      <circle cx="504" cy="285" r="106" fill="none" stroke="#9bcb3c" stroke-dasharray="4 5"/>
      <circle cx="504" cy="285" r="92" fill="#34a7d8"/>
      <circle cx="504" cy="285" r="74" fill="#ffffff"/>
      <rect x="474" y="268" width="44" height="44" fill="#9bcb3c"/>
      <rect x="518" y="282" width="18" height="30" fill="#9bcb3c"/>
      <g fill="#fff"><rect x="480" y="274" width="8" height="8"/><rect x="496" y="274" width="8" height="8"/><rect x="480" y="290" width="8" height="8"/><rect x="496" y="290" width="8" height="8"/></g>
      <rect x="478" y="254" width="30" height="10" fill="#9bcb3c" transform="rotate(-15 493 259)"/>
      <circle cx="636" cy="323" r="20" fill="#9bcb3c" stroke="#fff" stroke-width="3"/>
      <text x="636" y="330" text-anchor="middle" fill="#fff" font-family="Lato,sans-serif" font-size="18" font-weight="700">2</text>
    </g>
    <g>
      <circle cx="746" cy="348" r="106" fill="none" stroke="#9bcb3c" stroke-dasharray="4 5"/>
      <circle cx="746" cy="348" r="92" fill="#34a7d8"/>
      <circle cx="746" cy="348" r="74" fill="#ffffff"/>
      <rect x="722" y="318" width="48" height="60" rx="4" fill="#9bcb3c"/>
      <rect x="734" y="312" width="24" height="12" rx="3" fill="#7fb02a"/>
      <g stroke="#fff" stroke-width="3"><line x1="732" y1="338" x2="760" y2="338"/><line x1="732" y1="350" x2="760" y2="350"/><line x1="732" y1="362" x2="752" y2="362"/></g>
      <circle cx="790" cy="284" r="20" fill="#9bcb3c" stroke="#fff" stroke-width="3"/>
      <text x="790" y="291" text-anchor="middle" fill="#fff" font-family="Lato,sans-serif" font-size="18" font-weight="700">3</text>
    </g>
    <g>
      <circle cx="1003" cy="285" r="106" fill="none" stroke="#9bcb3c" stroke-dasharray="4 5"/>
      <circle cx="1003" cy="285" r="92" fill="#34a7d8"/>
      <circle cx="1003" cy="285" r="74" fill="#ffffff"/>
      <ellipse cx="1003" cy="295" rx="34" ry="25" fill="#9bcb3c"/>
      <rect x="985" y="312" width="8" height="14" fill="#9bcb3c"/><rect x="1013" y="312" width="8" height="14" fill="#9bcb3c"/>
      <circle cx="1003" cy="254" r="12" fill="#9bcb3c"/>
      <rect x="995" y="278" width="16" height="4" fill="#fff"/>
      <circle cx="1105" cy="348" r="20" fill="#9bcb3c" stroke="#fff" stroke-width="3"/>
      <text x="1105" y="355" text-anchor="middle" fill="#fff" font-family="Lato,sans-serif" font-size="18" font-weight="700">4</text>
    </g>
  </svg>
  <div class="step-label" style="left:82px;top:526px">Speak Consultant</div>
  <div class="step-label" style="left:374px;top:442px">Design</div>
  <div class="step-label" style="left:624px;top:460px">Schedule</div>
  <div class="step-label" style="left:902px;top:460px">Start Savings</div>
</section>

<section>
  <svg class="abs quote-badge" viewBox="0 0 92 92">
    <circle cx="46" cy="46" r="44" fill="#9bcb3c" stroke="#fff" stroke-width="4"/>
    <g fill="#fff"><rect x="27" y="42" width="16" height="16" rx="2"/><path d="M27,44 C27,34 32,29 41,28 L41,33 C36,34 34,37 34,44 Z"/><rect x="49" y="42" width="16" height="16" rx="2"/><path d="M49,44 C49,34 54,29 63,28 L63,33 C58,34 56,37 56,44 Z"/></g>
  </svg>
  <h2 class="abs section-title testi-title">What Our Client Say</h2>
  <div class="abs avatar" role="img" aria-label="Client portrait"></div>
  <p class="abs testi-text">Lorem Ipsum is simply dummy text of the printing and typesetting industry. Lorem Ipsum has been the industry's standard dummy text ever since the 1500s, when an unknown printer took a galley of type and scrambled it to make a type specimen book. It has survived not only five centuries.</p>
  <p class="abs testi-name">- MIRA DALEN</p>
</section>

<section class="abs split">
  <h2 class="split-title" style="left:78px">Other Section</h2>
  <h2 class="split-title" style="left:643px">Contact Form</h2>
  <div class="divider"></div>

  <div class="benefit" style="top:118px">
    <div class="benefit-icon"><svg width="34" height="34" viewBox="0 0 34 34"><circle cx="17" cy="17" r="14" fill="none" stroke="#fff" stroke-width="2.5"/><text x="17" y="22" text-anchor="middle" fill="#fff" font-size="13" font-family="Lato,sans-serif" font-weight="700">0%</text></svg></div>
    <div><h4>Zero Cost</h4><p>Lorem Ipsum is simply dummy text of the printing and typesetting industry. Lorem Ipsum has..<b>Read More</b></p></div>
  </div>
  <div class="benefit" style="top:212px">
    <div class="benefit-icon"><svg width="34" height="34" viewBox="0 0 34 34"><rect x="7" y="4" width="20" height="26" rx="2" fill="none" stroke="#fff" stroke-width="2.5"/><g stroke="#fff" stroke-width="2"><line x1="11" y1="12" x2="23" y2="12"/><line x1="11" y1="18" x2="23" y2="18"/><line x1="11" y1="24" x2="18" y2="24"/></g></svg></div>
    <div><h4>Lower Energy Bills</h4><p>Lorem Ipsum is simply dummy text of the printing and typesetting industry. Lorem Ipsum has..<b>Read More</b></p></div>
  </div>
  <div class="benefit" style="top:306px">
    <div class="benefit-icon"><svg width="34" height="34" viewBox="0 0 34 34"><circle cx="17" cy="17" r="9" fill="none" stroke="#fff" stroke-width="5" stroke-dasharray="4 3"/><circle cx="17" cy="17" r="4" fill="#fff"/></svg></div>
    <div><h4>No Maintenance</h4><p>Lorem Ipsum is simply dummy text of the printing and typesetting industry. Lorem Ipsum has..<b>Read More</b></p></div>
  </div>
</section>
<div class="field" style="top:2339px">Name*</div>
<div class="field" style="top:2396px">Phone No* :</div>
<div class="field" style="top:2453px;height:84px">Address* :</div>
<div class="field" style="top:2553px;width:212px">Pincode</div>
<div class="submit">SUBMIT</div>

<section>
  <h2 class="abs section-title blog-title">Latest Blog</h2>
  <article class="card" style="left:78px">
    <div class="card-img" role="img" aria-label="Couple standing beside rooftop solar panels" style="background:linear-gradient(135deg,#9fb9cf,#6f8ea6 50%,#d7c6a8)"></div>
    <div class="card-avatar" role="img" aria-label="Author portrait"></div>
    <div class="card-meta"><span class="card-date">10 August 2017</span><h3 class="card-head">Lorem Ipsum is simply dummy</h3></div>
    <p class="card-text">Lorem Ipsum is simply dummy text of the printing and typesetting industry. Lorem Ipsum has been the industry's standard dummy text ever since the 1500s,.......<b>READ MORE</b></p>
  </article>
  <article class="card" style="left:434px">
    <div class="card-img" role="img" aria-label="Open car on a road at sunset" style="background:linear-gradient(180deg,#f2d3a6,#e2a86c 45%,#6f5a48)"></div>
    <div class="card-avatar" role="img" aria-label="Author portrait"></div>
    <div class="card-meta"><span class="card-date">10 August 2017</span><h3 class="card-head">Lorem Ipsum is simply dummy</h3></div>
    <p class="card-text">Lorem Ipsum is simply dummy text of the printing and typesetting industry. Lorem Ipsum has been the industry's standard dummy text ever since the 1500s,.......<b>READ MORE</b></p>
  </article>
  <article class="card" style="left:790px">
    <div class="card-img" role="img" aria-label="Hand holding a green energy symbol beside a globe" style="background:linear-gradient(135deg,#2b2d2f,#5a5e60 55%,#8aa35a)"></div>
    <div class="card-avatar" role="img" aria-label="Author portrait"></div>
    <div class="card-meta"><span class="card-date">10 August 2017</span><h3 class="card-head">Lorem Ipsum is simply dummy</h3></div>
    <p class="card-text">Lorem Ipsum is simply dummy text of the printing and typesetting industry. Lorem Ipsum has been the industry's standard dummy text ever since the 1500s,.......<b>READ MORE</b></p>
  </article>
</section>

<footer class="abs footer">
  <svg class="abs" style="left:0;top:0" width="1200" height="440" viewBox="0 0 1200 440">
    <defs><linearGradient id="footGrad" x1="0" y1="0" x2="0" y2="1"><stop offset="0" stop-color="#2f3538"/><stop offset="1" stop-color="#1c1f21"/></linearGradient></defs>
    <path d="M0,40 C200,110 380,0 600,50 C820,100 1000,10 1200,70 L1200,440 L0,440 Z" fill="url(#footGrad)"/>
  </svg>
  <div class="foot-col" style="left:78px;top:150px;width:300px">
    <div class="foot-brand"><span class="brand-dot"></span><span class="brand-name">HELIOMA ENERGY</span></div>
    <p>Lorem Ipsum is simply dummy text of the printing and typesetting industry. Lorem Ipsum has been the industry's</p>
  </div>
  <div class="foot-col" style="left:418px;top:170px">
    <h4>Useful Link</h4>
    <p>Home<br>Why Helioma Energy<br>How it Works<br>Testimonial<br>Blog<br>Contact</p>
  </div>
  <div class="foot-col" style="left:636px;top:170px;width:260px">
    <h4>Contact Info</h4>
    <div class="foot-row"><svg width="16" height="20" viewBox="0 0 16 20"><path d="M8,0 a8,8 0 0 1 8,8 c0,6 -8,12 -8,12 s-8,-6 -8,-12 a8,8 0 0 1 8,-8 Z" fill="#fff"/><circle cx="8" cy="8" r="3" fill="#2a2f33"/></svg><span>Lorem Ipsum is simply dummy text of the printing dummy.</span></div>
    <div class="foot-row"><svg width="16" height="16" viewBox="0 0 16 16"><path d="M3,1 L6,1 L7,5 L5,6.5 C6,9 7,10 9.5,11 L11,9 L15,10 L15,13 C15,14 14,15 13,15 C6,15 1,10 1,3 C1,2 2,1 3,1 Z" fill="#fff"/></svg><span>555.014.2290</span></div>
    <div class="foot-row"><svg width="18" height="14" viewBox="0 0 18 14"><rect x="0" y="0" width="18" height="14" fill="#fff"/><path d="M0,0 L9,8 L18,0" fill="none" stroke="#2a2f33" stroke-width="1.5"/></svg><span>info@heliomaenergy.com</span></div>
    <div class="foot-row"><svg width="16" height="16" viewBox="0 0 16 16"><circle cx="8" cy="8" r="7" fill="none" stroke="#fff" stroke-width="1.5"/><ellipse cx="8" cy="8" rx="3" ry="7" fill="none" stroke="#fff" stroke-width="1.2"/><line x1="1" y1="8" x2="15" y2="8" stroke="#fff" stroke-width="1.2"/></svg><span>www.heliomaenergy.com</span></div>
  </div>
  <div class="foot-col" style="left:934px;top:170px">
    <h4>Follow us on</h4>
    <div class="social"><i class="first"></i>Circlebook</div>
    <div class="social"><i></i>Chirpline</div>
    <div class="social"><i></i>Linkpro</div>
    <div class="social"><i></i>Snapgram</div>
  </div>
</footer>
<div class="abs bottom-bar"><b>HELIOMA ENERGY</b> | Copyright 2017, All Rights Reserved</div>

</body>
</html>
```